TL - business card

Tallow Partners is an insurance brokerage firm, inovative, proactive, vigorous, which aims to become the leader of the insurance brokers in Anfrica. We should like to get some designs which should be avoided also in Gray / Metallic for the Administration and Orange / Blue for the Managers (ike in the picture sent). The Blue / Green logo is not the correct one, but the source of the file. Please adjust the color accordingly for the business cards. 1 / Orange / Blue 2 / Gray / Metallic We want something classic but which is transmitted strenght, inovation, modernity and most of all, rapidity. We want something start-up like, very punchy and catching eye remaining profesional at the same time. Name: Dorian Whitlock Function: Managing Director Address: N ° 17/18 Rua Veloso - R / C 2B Direita - Bairro Mutamba - Luanda Tel: (+244) 947 582 316 Email: dorian.whitlock@tallow-p.example Website: www.tallow-p. example We want classic in the front and creative, colorfull at the back. The cards will be printed in relief, with very high quality of paper.
Insurance Broker
Colors
Designer to choose colors to be used in the design.

```html
<!DOCTYPE html>
<html lang="en">
<head>
<meta charset="utf-8">
<title>TL – Business Card</title>
<link rel="stylesheet" href="https://fonts.googleapis.com/css2?family=Montserrat:wght@400;500;600;700&display=swap">
<style>
  :root {
    --backdrop: #2a2a2c;
    --card-white: #ffffff;
    --brand-blue: #25a8e0;
    --brand-green: #0e9444;
    --text-grey: #5a5a5a;
  }
  * { margin: 0; padding: 0; box-sizing: border-box; }
  html, body {
    width: 1200px;
    height: 900px;
    overflow: hidden;
    background: var(--backdrop);
    font-family: "Montserrat", sans-serif;
  }
  .canvas {
    width: 1200px;
    height: 900px;
    display: flex;
    flex-direction: column;
    align-items: center;
    justify-content: center;
    gap: 60px;
  }
  .card {
    position: relative;
    width: 620px;
    height: 354px;
    border-radius: 20px;
    overflow: hidden;
    box-shadow: 0 14px 30px rgba(0,0,0,0.45);
  }

  /* Front */
  .card-front { background: var(--card-white); }
  .card-front .accent-band {
    position: absolute;
    inset: 0;
    width: 100%;
    height: 100%;
  }
  .brand-lockup {
    position: absolute;
    left: 150px;
    top: 34px;
    display: flex;
    align-items: center;
    gap: 12px;
  }
  .brand-dot {
    width: 30px;
    height: 30px;
    border-radius: 50%;
    background: var(--brand-green);
  }
  .brand-name {
    font-weight: 700;
    font-size: 24px;
    letter-spacing: 0.5px;
    text-transform: uppercase;
    color: var(--brand-green);
  }
  .contact {
    position: absolute;
    left: 34px;
    top: 100px;
    color: var(--text-grey);
  }
  .contact .person {
    font-weight: 600;
    font-size: 28px;
    color: var(--brand-blue);
    line-height: 1.1;
  }
  .contact .role {
    font-size: 14px;
    font-weight: 500;
    margin: 4px 0 12px;
  }
  .contact .address {
    font-size: 13px;
    line-height: 1.45;
    margin-bottom: 8px;
  }
  .contact .line {
    display: flex;
    align-items: center;
    gap: 8px;
    font-size: 13px;
    line-height: 1.6;
  }
  .contact .line svg { width: 12px; height: 12px; flex: none; }

  /* Back */
  .card-back {
    background: var(--brand-blue);
    display: flex;
    align-items: center;
    justify-content: center;
    gap: 16px;
  }
  .card-back .brand-dot { width: 46px; height: 46px; background: var(--card-white); }
  .card-back .brand-name { font-size: 40px; color: var(--card-white); }
</style>
</head>
<body>
<main class="canvas">

  <section class="card card-front" aria-label="Business card front">
    <svg class="accent-band" viewBox="0 0 620 354" preserveAspectRatio="none" aria-hidden="true">
      <polygon points="170,354 620,150 620,354" fill="#0e9444"/>
      <polygon points="250,318 620,190 620,150 210,336" fill="#25a8e0" opacity="0.9"/>
    </svg>

    <div class="brand-lockup">
      <span class="brand-dot"></span>
      <span class="brand-name">Tallow Partners</span>
    </div>

    <div class="contact">
      <p class="person">Dorian Whitlock</p>
      <p class="role">Managing Director</p>
      <p class="address">
        N ° 17/18 Rua Veloso<br>
        R / C 2B Direita<br>
        Bairro Mutamba - Luanda
      </p>
      <p class="line">
        <svg viewBox="0 0 24 24" aria-hidden="true"><path fill="#25a8e0" d="M6.6 10.8a15.1 15.1 0 0 0 6.6 6.6l2.2-2.2c.3-.3.7-.4 1-.2 1.1.4 2.3.6 3.6.6.6 0 1 .4 1 1V20c0 .6-.4 1-1 1A17 17 0 0 1 3 4c0-.6.4-1 1-1h3.5c.6 0 1 .4 1 1 0 1.3.2 2.5.6 3.6.1.3 0 .7-.2 1z"/></svg>
        (+244) 947 582 316
      </p>
      <p class="line">
        <svg viewBox="0 0 24 24" aria-hidden="true"><rect x="2" y="5" width="20" height="14" rx="2" fill="none" stroke="#25a8e0" stroke-width="2"/><path d="M3 6l9 7 9-7" fill="none" stroke="#25a8e0" stroke-width="2"/></svg>
        dorian.whitlock@tallow-p.example
      </p>
    </div>
  </section>

  <section class="card card-back" aria-label="Business card back">
    <span class="brand-dot"></span>
    <span class="brand-name">Tallow Partners</span>
  </section>

</main>
</body>
</html>
```